Thornbury Building Company - Card Design

I am looking to use the logo designs that you already did for me to develop a business card. I would like the card to have a black background and be double sided. I want white and green logo and text. I have attached an inspiration photo of a look that I like. I would like to use the Vertical Logo attached to take up the full front side of the card. On the back where I have my name and information, I would like to have the horizontal logo or maybe even just the image of the 'A' and trees without the text. I am open, but I am looking for something clean and simple and I want the green to really pop! Additional files can be found under Design #: 58302946

Target Market(s)

Homeowners

Industry/Entity Type

Construction

Contact Information for Business Card

Name: Marcus Thornbury, Title: Project Manager, Phone: 555.274.8136, Email: thornburybuildingcompany@mailvesta.com, address: 487 Larkspur Ln, Alderwick, OR 95033, Lic# 2468317

Colors
00AB8E
00BBA5
67D7C9
C6EFE9
E9F9F6

Requirements
Nice to have
• I would like to see the logos that I have already got from ArtLoomHub, though I am open to new ones

```html
<!DOCTYPE html>
<html lang="en">
<head>
<meta charset="utf-8">
<title>Thornbury Building Company – Business Card</title>
<link href="https://fonts.googleapis.com/css2?family=Lato:wght@400;700;900&display=swap" rel="stylesheet">
<style>
  :root {
    --stage: #2b2b2d;
    --card: #222022;
    --green: #6cb83f;
    --white: #ffffff;
    --soft: #e6e6e6;
  }
  * { box-sizing: border-box; margin: 0; padding: 0; }
  html, body { width: 1200px; height: 875px; overflow: hidden; }
  body {
    background: var(--stage);
    font-family: "Lato", sans-serif;
    position: relative;
  }
  .card {
    position: absolute;
    top: 289px;
    width: 520px;
    height: 297px;
    background: var(--card);
    border-radius: 16px;
    box-shadow: 0 18px 40px rgba(0,0,0,.45);
    overflow: hidden;
  }
  .card--front { left: 45px; }
  .card--back { left: 635px; }

  /* Front */
  .front-lockup {
    position: absolute;
    inset: 0;
    display: flex;
    flex-direction: column;
    align-items: center;
    justify-content: center;
  }
  .estd-row {
    display: flex;
    justify-content: space-between;
    width: 360px;
    margin-bottom: 14px;
  }
  .estd {
    color: var(--white);
    font-size: 11px;
    letter-spacing: 4px;
    border-bottom: 1px solid var(--green);
    padding-bottom: 3px;
  }
  .front-mark {
    width: 34px; height: 34px;
    background: var(--green);
    margin-bottom: 14px;
  }
  .front-name {
    color: var(--white);
    font-weight: 900;
    font-size: 44px;
    letter-spacing: 1px;
    line-height: 1;
    text-transform: uppercase;
  }
  .front-sub {
    color: var(--white);
    font-weight: 900;
    font-size: 20px;
    letter-spacing: 6px;
    margin-top: 6px;
    text-transform: uppercase;
  }

  /* Back */
  .back-lockup {
    position: absolute;
    left: 40px;
    top: 40px;
    display: flex;
    align-items: center;
    gap: 14px;
  }
  .back-mark { width: 22px; height: 22px; background: var(--green); }
  .back-name {
    color: var(--white);
    font-weight: 900;
    font-size: 22px;
    letter-spacing: .5px;
    text-transform: uppercase;
    white-space: nowrap;
  }
  .contact {
    position: absolute;
    left: 76px;
    top: 96px;
  }
  .person-name {
    color: var(--green);
    font-weight: 900;
    font-size: 20px;
    text-transform: uppercase;
  }
  .person-title {
    color: var(--white);
    font-weight: 700;
    font-size: 13px;
    margin-bottom: 12px;
  }
  .contact-list { list-style: none; }
  .contact-item {
    display: flex;
    align-items: flex-start;
    gap: 8px;
    color: var(--soft);
    font-size: 12.5px;
    line-height: 1.45;
    white-space: nowrap;
  }
  .contact-item svg { width: 11px; height: 11px; margin-top: 4px; flex: none; fill: var(--green); }
  .license {
    color: var(--soft);
    font-size: 12.5px;
    margin-top: 12px;
    padding-left: 19px;
  }
</style>
</head>
<body>
  <section class="card card--front" aria-label="Card front">
    <div class="front-lockup">
      <div class="estd-row"><span class="estd">ESTD</span><span class="estd">2020</span></div>
      <div class="front-mark" aria-hidden="true"></div>
      <div class="front-name">Thornbury</div>
      <div class="front-sub">Building Company</div>
    </div>
  </section>

  <section class="card card--back" aria-label="Card back">
    <div class="back-lockup">
      <div class="back-mark" aria-hidden="true"></div>
      <div class="back-name">Thornbury Building Company</div>
    </div>
    <div class="contact">
      <div class="person-name">Marcus Thornbury</div>
      <div class="person-title">Project Manager</div>
      <ul class="contact-list">
        <li class="contact-item">
          <svg viewBox="0 0 12 12" aria-hidden="true"><path d="M6 0a4 4 0 0 0-4 4c0 3 4 8 4 8s4-5 4-8a4 4 0 0 0-4-4zm0 5.5A1.5 1.5 0 1 1 6 2.5a1.5 1.5 0 0 1 0 3z"/></svg>
          <span>487 Larkspur Ln<br>Alderwick, OR 95033</span>
        </li>
        <li class="contact-item">
          <svg viewBox="0 0 12 12" aria-hidden="true"><path d="M2.5 0.5l2 2.5-1.2 1.3a7 7 0 0 0 4.4 4.4L9 7.5l2.5 2-1.3 2C5 11.5 .5 7 .5 1.8z"/></svg>
          <span>555.274.8136</span>
        </li>
        <li class="contact-item">
          <svg viewBox="0 0 12 12" aria-hidden="true"><path d="M0 2h12v8H0zM1 3l5 3.5L11 3z" fill-rule="evenodd"/></svg>
          <span>thornburybuildingcompany@mailvesta.com</span>
        </li>
        <li class="contact-item">
          <svg viewBox="0 0 12 12" aria-hidden="true"><circle cx="6" cy="6" r="5.5"/></svg>
          <span>thornburybuildingcompany.com</span>
        </li>
      </ul>
      <div class="license">Lic# 2468317</div>
    </div>
  </section>
</body>
</html>
```